Website for Excavator and Earthworks Company

We require a modern, sleek and practical website for our newly created earthworks/excavator business in Perth, Western Australia called Bluegum Ridge Earthworks.

The website should have a modern, cutting edge feel but only needs to be relatively simplistic in it's layout and eventual functionality.

Some pages it should have would be Home, About, Projects and Contact Us.

```html
<!DOCTYPE html>
<html lang="en">
<head>
<meta charset="utf-8">
<title>Bluegum Ridge Earthworks</title>
<link href="https://fonts.googleapis.com/css2?family=Archivo:wght@400;500;600;700;800&family=Inter:wght@400;500;600&display=swap" rel="stylesheet">
<style>
:root{
  --lime:#c8dc00;
  --ink:#121212;
  --dark:#151515;
  --white:#ffffff;
}
*{margin:0;padding:0;box-sizing:border-box}
html,body{width:1200px;height:3492px;overflow:hidden;background:var(--ink);color:var(--white);font-family:"Inter",sans-serif}
.page{position:relative;width:1200px;height:3492px}
section,header,footer{position:absolute;left:0;width:1200px}
.abs{position:absolute}
.head{font-family:"Archivo",sans-serif;font-weight:700;text-transform:uppercase}
.brand{display:flex;align-items:center;gap:10px;font-family:"Archivo",sans-serif;font-weight:800;font-size:15px;letter-spacing:.3px;color:var(--white);text-transform:uppercase;white-space:nowrap}
.brand-mark{width:30px;height:30px;background:var(--lime);flex:none}
.btn{position:absolute;display:flex;align-items:center;justify-content:center;font-family:"Archivo",sans-serif;font-weight:600;font-size:11px;text-transform:uppercase}
.btn-lime{background:var(--lime);color:var(--ink)}
.btn-outline{border:1px solid var(--lime);color:var(--lime)}
.btn-white{background:var(--white);color:var(--ink)}

/* hero */
.hero{top:0;height:563px;background:linear-gradient(180deg,#3a2410 0%,#b8621a 22%,#e08a2a 38%,#7a4212 58%,#1d140c 78%,#111 100%)}
.nav{top:24px;font-family:"Archivo",sans-serif;font-size:12px;font-weight:500}
.nav a{position:absolute;color:var(--white);text-decoration:none;white-space:nowrap}
.nav a.active{color:var(--lime);text-decoration:underline}
.hero-title{top:228px;width:1200px;text-align:center;font-size:40px;line-height:44px;text-shadow:0 2px 8px rgba(0,0,0,.5)}
.hero-sub{top:328px;left:320px;width:560px;text-align:center;font-family:"Archivo",sans-serif;font-size:12px;line-height:19px;letter-spacing:1.6px;text-transform:uppercase;font-weight:500}

/* about */
.about{top:563px;height:563px;background:var(--dark)}
.about-kicker{left:172px;top:110px;font-family:"Archivo",sans-serif;color:var(--lime);font-size:22px}
.about-name{left:172px;top:140px;font-family:"Archivo",sans-serif;font-weight:800;font-size:19px;text-transform:uppercase}
.about-body{left:50px;top:193px;width:490px}
.about-copy{font-size:11px;line-height:19px;color:var(--white)}
.about-copy p{margin-bottom:19px}
.tags{display:flex;gap:32px;margin-top:14px;font-family:"Archivo",sans-serif;font-weight:700;font-size:13px}
.tags span{display:flex;align-items:center;gap:10px}
.video{left:625px;top:93px;width:575px;height:375px;background:linear-gradient(180deg,#8aa3b5 0%,#c9b08a 45%,#7a5a3a 75%,#4a3624 100%)}
.play{position:absolute;left:95px;top:149px;width:76px;height:76px;border-radius:50%;background:var(--lime);display:flex;align-items:center;justify-content:center}
.play i{width:62px;height:62px;border-radius:50%;background:#111;display:flex;align-items:center;justify-content:center}

/* services */
.services{top:1126px;height:518px;background:linear-gradient(180deg,#2e2925,#3a322c 50%,#2b2622)}
.section-title{font-size:22px}
.services .section-title{top:86px;width:1200px;text-align:center}
.card{top:145px;width:338px;height:286px;overflow:hidden}
.card-label{position:absolute;left:0;right:0;bottom:22px;text-align:center;font-family:"Archivo",sans-serif;font-weight:700;font-size:16px;text-transform:uppercase}
.card-c1{left:50px;background:linear-gradient(160deg,#f4d27a,#c98a2a 40%,#3a2c20 80%,#1a1510)}
.card-c2{left:431px;background:linear-gradient(180deg,#7a7066,#4a4038 60%,#1a1612)}
.card-c3{left:811px;background:linear-gradient(180deg,#e9e2d4,#c6a27a 50%,#4a3a2a 85%,#201810)}
.card-c2 .card-label{bottom:92px;color:var(--lime)}
.card-desc{position:absolute;left:30px;right:30px;bottom:24px;text-align:center;font-size:11.5px;line-height:19px}

/* projects */
.projects{top:1644px;height:797px;background:var(--ink)}
.projects .section-title{left:50px;top:88px}
.arrow{position:absolute;top:89px;width:26px;height:26px;border-radius:50%;display:flex;align-items:center;justify-content:center}
.arrow-prev{left:957px;border:1px solid var(--lime)}
.arrow-next{left:996px;background:var(--lime)}
.tile{position:absolute}

/* contact */
.contact{top:2441px;height:648px;background:linear-gradient(180deg,#2c2c2c,#1e1e1e)}
.contact-title{left:50px;top:91px;font-size:30px;line-height:35px}
.contact-sub{left:50px;top:170px;font-size:22px;line-height:35px;font-weight:600}
.info{left:50px;display:flex;gap:12px;font-size:11.5px;line-height:15px;font-weight:500}
.info b{display:block;font-weight:600}
.info-icon{width:26px;height:26px;border-radius:50%;background:var(--lime);flex:none;display:flex;align-items:center;justify-content:center}
.form{left:743px;top:92px;width:407px;height:463px;background:var(--lime);color:var(--ink);padding:38px 38px 0}
.form h2{font-family:"Archivo",sans-serif;font-weight:600;font-size:22px;text-transform:uppercase;margin-bottom:20px}
.row{display:flex;gap:17px}
.field{flex:1;margin-bottom:14px}
.field label{display:block;font-size:10px;font-weight:600;margin-bottom:5px}
.field .input{height:29px;background:var(--white);font-size:10px;color:#999;padding:8px 9px}
.field .select{display:flex;justify-content:space-between;align-items:center}
.field .area{height:88px}
.submit{height:30px;background:#0d0d0d;color:var(--white);font-family:"Archivo",sans-serif;font-weight:700;font-size:10px;display:flex;align-items:center;justify-content:center}

/* footer */
.footer{top:3089px;height:403px;background:linear-gradient(180deg,#181818,#242220 60%,#2a2622)}
.footer-rule{left:50px;top:27px;width:1100px;height:1px;background:rgba(255,255,255,.12)}
.footer-brand{top:110px;width:1200px;justify-content:center;font-size:17px}
.footer-nav{top:192px;width:1200px;display:flex;justify-content:center;gap:54px;font-family:"Archivo",sans-serif;font-size:14px;text-transform:uppercase}
.socials{top:241px;width:1200px;display:flex;justify-content:center;gap:14px}
.socials span{width:38px;height:38px;border-radius:50%;background:var(--lime)}
.copy{top:358px;width:1200px;text-align:center;font-size:10px;letter-spacing:.6px;font-family:"Archivo",sans-serif}
</style>
</head>
<body>
<div class="page">

<header class="hero" role="img" aria-label="Excavator silhouette against an orange sunset sky">
  <div class="abs brand" style="left:50px;top:16px"><span class="brand-mark"></span>Bluegum Ridge Earthworks</div>
  <nav class="nav abs" style="left:0;width:1200px">
    <a class="active" style="left:416px">HOME</a>
    <a style="left:506px">ABOUT US</a>
    <a style="left:620px">PROJECT</a>
    <a style="left:728px">CONTACT US</a>
  </nav>
  <span class="btn btn-outline" style="left:917px;top:15px;width:103px;height:34px">Get a quote</span>
  <span class="btn btn-white" style="left:1032px;top:15px;width:118px;height:34px">(08) 9000 1234</span>
  <h1 class="abs head hero-title">Professional Earthworks &amp;<br>Excavation in Perth</h1>
  <p class="abs hero-sub">Bluegum Ridge Earthworks delivers expert excavation, site preparation, and land development services across Western Australia with precision, safety, and efficiency.</p>
  <span class="btn btn-lime" style="left:484px;top:407px;width:103px;height:33px">Get a quote</span>
  <span class="btn btn-white" style="left:599px;top:407px;width:117px;height:33px">(08) 9000 1234</span>
</header>

<section class="about">
  <span class="abs brand-mark" style="left:50px;top:111px;width:50px;height:50px"></span>
  <div class="abs about-kicker">About</div>
  <div class="abs about-name">Bluegum Ridge</div>
  <div class="abs about-body">
    <div class="about-copy">
      <p>Founded in Perth, Western Australia, Bluegum Ridge Earthworks brings together decades of experience in the excavation and earthmoving industry. Our team of certified operators and project managers are committed to delivering exceptional results for every client.</p>
      <p>We pride ourselves on our commitment to safety, environmental responsibility, and customer satisfaction. Using state-of-the-art equipment and proven techniques, we tackle projects ranging from small residential jobs to large-scale commercial developments.</p>
      <p>At Bluegum Ridge, we understand that successful earthworks require more than just heavy machinery—they require expertise, precision, and a deep understanding of local soil conditions and regulations.</p>
    </div>
    <div class="tags">
      <span><svg width="26" height="22" viewBox="0 0 26 22"><path d="M13 1 1 11h4v10h6v-6h4v6h6V11h4z" fill="#c8dc00"/></svg>RESIDENTIAL</span>
      <span><svg width="18" height="22" viewBox="0 0 18 22"><path d="M1 1h16v20h-6v-4H7v4H1z" fill="#c8dc00"/><path d="M4 4h3v3H4zm7 0h3v3h-3zM4 10h3v3H4zm7 0h3v3h-3z" fill="#151515"/></svg>COMMERCIAL</span>
    </div>
  </div>
  <div class="abs video" role="img" aria-label="Workers in safety vests on a rocky site with excavators at sunset">
    <span class="play"><i><svg width="22" height="24" viewBox="0 0 22 24"><path d="M2 1l19 11L2 23z" fill="#c8dc00"/></svg></i></span>
  </div>
</section>

<section class="services" role="img" aria-label="Dim background of earthmoving machinery">
  <h2 class="abs head section-title">Our Services</h2>
  <div class="abs card card-c1" role="img" aria-label="Excavator bucket pouring soil in sunlight"><div class="card-label">Site Preparation</div></div>
  <div class="abs card card-c2" role="img" aria-label="Excavator digging a deep trench">
    <div class="card-label">Excavation &amp; Trenching</div>
    <p class="card-desc">Precise excavation for foundations, utilities, drainage, and more. Our experienced operators handle projects of all sizes.</p>
  </div>
  <div class="abs card card-c3" role="img" aria-label="Engineers reviewing plans under a steel frame"><div class="card-label">Land Development</div></div>
</section>

<section class="projects">
  <h2 class="abs head section-title">Our Projects</h2>
  <span class="arrow arrow-prev"><svg width="8" height="8" viewBox="0 0 8 8"><path d="M6 0v8L1 4z" fill="#c8dc00"/></svg></span>
  <span class="arrow arrow-next"><svg width="8" height="8" viewBox="0 0 8 8"><path d="M2 0v8l5-4z" fill="#121212"/></svg></span>
  <div class="tile" style="left:50px;top:143px;width:320px;height:197px;background:linear-gradient(180deg,#9ec0e0,#b8b4ac 55%,#7a7268)" role="img" aria-label="Excavator on demolition rubble with city towers"></div>
  <div class="tile" style="left:50px;top:340px;width:320px;height:373px;background:linear-gradient(180deg,#2a6fd0,#6fa0d8 40%,#a8764a 70%,#5a3e26)" role="img" aria-label="Excavator loading a dump truck under blue sky"></div>
  <div class="tile" style="left:370px;top:143px;width:487px;height:319px;background:linear-gradient(180deg,#c8c0b4,#7a6a52 45%,#b8803a 75%,#4a3422)" role="img" aria-label="Piling rig and concrete pillars on a construction site"></div>
  <div class="tile" style="left:857px;top:143px;width:293px;height:319px;background:linear-gradient(180deg,#e0d8cc,#7a8a86 45%,#c89a4a 70%,#8a6a4a)" role="img" aria-label="Yellow excavator with mountains behind"></div>
  <div class="tile" style="left:370px;top:462px;width:391px;height:251px;background:linear-gradient(180deg,#5a86c4,#c8d4e0 40%,#c8aa82 70%,#8a6e50)" role="img" aria-label="Excavator loading a truck near the coast"></div>
  <div class="tile" style="left:761px;top:462px;width:389px;height:251px;background:linear-gradient(180deg,#b8c8d8,#d8d0c4 40%,#b88a4a 65%,#6a5036)" role="img" aria-label="Excavator and articulated dump truck moving soil"></div>
</section>

<section class="contact" role="img" aria-label="Dim background of an excavator on site">
  <h2 class="abs head contact-title">Ready to start your<br>earthworks project?</h2>
  <p class="abs head contact-sub">Get in touch with our team for a free,<br>no-obligation quote.</p>
  <div class="abs info" style="top:265px"><span class="info-icon"><svg width="12" height="14" viewBox="0 0 12 14"><path d="M6 1a4.5 4.5 0 0 0-4.5 4.5C1.5 9 6 13 6 13s4.5-4 4.5-7.5A4.5 4.5 0 0 0 6 1z" fill="none" stroke="#121212" stroke-width="1.5"/><circle cx="6" cy="5.5" r="1.5" fill="#121212"/></svg></span><div><b>Address</b>Perth, Western Australia<br>Serving the greater Perth region and beyond</div></div>
  <div class="abs info" style="top:335px"><span class="info-icon"><svg width="13" height="13" viewBox="0 0 13 13"><path d="M3 1l2 3-1.3 1.3a7 7 0 0 0 4 4L9 8l3 2-1.5 2C6 12 1 7 1 2.5z" fill="none" stroke="#121212" stroke-width="1.4"/></svg></span><div><b>Phone</b>(08) 9000 5678</div></div>
  <div class="abs info" style="top:395px"><span class="info-icon"><svg width="13" height="10" viewBox="0 0 13 10"><rect x="1" y="1" width="11" height="8" fill="none" stroke="#121212" stroke-width="1.4"/><path d="M1 1l5.5 4L12 1" fill="none" stroke="#121212" stroke-width="1.4"/></svg></span><div><b>Email</b>info@bluegumridgeearthworks.com.au</div></div>
  <div class="abs info" style="top:456px"><span class="info-icon"><svg width="13" height="13" viewBox="0 0 13 13"><circle cx="6.5" cy="6.5" r="5.3" fill="none" stroke="#121212" stroke-width="1.4"/><path d="M6.5 3.5v3l2 1.5" fill="none" stroke="#121212" stroke-width="1.4"/></svg></span><div><b>Business Hours</b>Monday - Friday: 7:00 AM - 5:00 PM<br>Saturday: 8:00 AM - 12:00 PM<br>Emergency services available</div></div>

  <div class="abs form">
    <h2>Get in touch</h2>
    <div class="row">
      <div class="field"><label>First Name*</label><div class="input">Enter your first name</div></div>
      <div class="field"><label>Last Name*</label><div class="input">Enter your last name</div></div>
    </div>
    <div class="row">
      <div class="field"><label>Phone*</label><div class="input">Enter your phone</div></div>
      <div class="field"><label>Email*</label><div class="input">Enter your email</div></div>
    </div>
    <div class="field" style="margin-top:14px"><label>Service Required</label><div class="input select">Site Preparation<svg width="8" height="5" viewBox="0 0 8 5"><path d="M0 0h8L4 5z" fill="#121212"/></svg></div></div>
    <div class="field"><label>Message</label><div class="input area"></div></div>
    <div class="submit">SUBMIT</div>
  </div>
</section>

<footer class="footer" role="img" aria-label="Dim background of trucks and loaders">
  <div class="abs footer-rule"></div>
  <div class="abs brand footer-brand"><span class="brand-mark"></span>Bluegum Ridge Earthworks</div>
  <nav class="abs footer-nav"><span>Home</span><span>About Us</span><span>Our Services</span><span>Projects</span><span>Contact</span></nav>
  <div class="abs socials"><span aria-label="Social profile one"></span><span aria-label="Social profile two"></span></div>
  <p class="abs copy">© 2026 BLUEGUM RIDGE EARTHWORKS. ALL RIGHTS RESERVED.</p>
</footer>

</div>
</body>
</html>
```